Mindfulness School for Children -- Business Cards

We're looking for business cards for our school directors and owners. We're a mindfulness school for children called little lanterns. Attached are our logos/icons.

```html
<!DOCTYPE html>
<html lang="en">
<head>
<meta charset="utf-8">
<title>little lanterns — Business Cards</title>
<link href="https://fonts.googleapis.com/css2?family=Lora:wght@400&family=Montserrat:wght@500;700&family=Arimo:wght@400&display=swap" rel="stylesheet">
<style>
  :root {
    --bg: #2a2a2a;
    --bg-edge: #141414;
    --paper: #ffffff;
    --mist: #eef2f3;
    --green-dark: #58a08e;
    --green-light: #94cc9c;
    --blue-dark: #5fb6cb;
    --blue-light: #93d8ec;
    --brand-teal: #5aa69a;
    --ink: #111111;
  }
  * { box-sizing: border-box; margin: 0; padding: 0; }
  html, body { width: 1200px; height: 1015px; overflow: hidden; }
  body {
    background: radial-gradient(ellipse at 50% 45%, var(--bg) 0%, #1e1e1e 60%, var(--bg-edge) 100%);
    position: relative;
    font-family: "Arimo", Arial, sans-serif;
  }
  .card {
    position: absolute;
    width: 700px;
    height: 400px;
    overflow: hidden;
    box-shadow: 0 18px 40px rgba(0,0,0,0.55);
  }

  /* Front */
  .card-front {
    left: 60px; top: 60px;
    background:
      radial-gradient(ellipse at 30% 40%, #f6f8f9 0%, transparent 55%),
      radial-gradient(ellipse at 70% 70%, #e9eef0 0%, transparent 60%),
      var(--mist);
    display: flex; flex-direction: column; align-items: center; justify-content: center;
  }
  .front-brand {
    display: flex; align-items: center; gap: 14px;
    font-family: "Lora", Georgia, serif;
    font-size: 62px; color: var(--brand-teal); letter-spacing: 0.5px;
  }
  .brand-dot { width: 16px; height: 16px; border-radius: 50%; background: var(--brand-teal); }
  .front-web {
    margin-top: 34px;
    font-size: 15px; letter-spacing: 5px; color: var(--brand-teal);
  }

  /* Back */
  .card-back { left: 440px; top: 520px; background: var(--paper); }
  .band-green {
    position: absolute; left: 0; top: 0; width: 100%; height: 172px;
    background: linear-gradient(100deg, var(--green-dark) 0%, var(--green-light) 100%);
    display: flex; align-items: center; justify-content: center;
  }
  .back-brand {
    display: flex; align-items: center; gap: 12px;
    font-family: "Lora", Georgia, serif;
    font-size: 58px; color: var(--paper);
  }
  .back-brand .brand-dot { background: var(--paper); }
  .band-blue {
    position: absolute; left: 0; top: 172px; width: 100%; height: 128px;
    background: linear-gradient(100deg, var(--blue-dark) 0%, var(--blue-light) 100%);
    display: flex; align-items: center; padding-left: 92px;
  }
  .person { text-align: right; color: var(--paper); font-family: "Montserrat", Arial, sans-serif; }
  .person-name { font-weight: 700; font-size: 27px; line-height: 1.1; }
  .person-role { font-weight: 500; font-size: 18px; }
  .divider { width: 2px; height: 60px; background: var(--paper); margin: 0 24px; }
  .contacts { list-style: none; color: var(--paper); font-size: 17px; line-height: 1.45; }
  .contacts li { display: flex; align-items: center; gap: 10px; }
  .contacts svg { width: 18px; height: 18px; flex: none; }
  .band-white {
    position: absolute; left: 0; top: 300px; width: 100%; height: 84px;
    display: flex; align-items: center; justify-content: center;
    font-size: 22px; color: var(--ink); letter-spacing: 0.3px;
  }
  .strip { position: absolute; bottom: 0; height: 16px; }
  .strip-green { left: 0; width: 52%; background: linear-gradient(90deg, var(--green-dark), var(--green-light)); }
  .strip-blue { right: 0; width: 47.5%; background: linear-gradient(90deg, var(--blue-dark), var(--blue-light)); }
</style>
</head>
<body>

  <section class="card card-front" aria-label="Business card front">
    <div class="front-brand"><span class="brand-dot"></span><span>little lanterns</span></div>
    <p class="front-web">www.lanternschool.com</p>
  </section>

  <section class="card card-back" aria-label="Business card back">
    <div class="band-green">
      <div class="back-brand"><span class="brand-dot"></span><span>little lanterns</span></div>
    </div>
    <div class="band-blue">
      <div class="person">
        <p class="person-name">Daniel Hartley</p>
        <p class="person-role">Managing Director</p>
      </div>
      <span class="divider"></span>
      <ul class="contacts">
        <li>
          <svg viewBox="0 0 24 24" fill="none" stroke="#fff" stroke-width="2.2" stroke-linecap="round" stroke-linejoin="round"><path d="M5 3h4l2 5-2.5 1.5a11 11 0 0 0 6 6L16 13l5 2v4a2 2 0 0 1-2 2A16 16 0 0 1 3 5a2 2 0 0 1 2-2z"/></svg>
          044-321 654 987
        </li>
        <li>
          <svg viewBox="0 0 24 24" fill="none" stroke="#fff" stroke-width="2.2" stroke-linejoin="round"><rect x="2" y="5" width="20" height="14"/><path d="M2 5l10 8 10-8"/></svg>
          info@lanternmail.com
        </li>
        <li>
          <svg viewBox="0 0 24 24" fill="none" stroke="#fff" stroke-width="2"><circle cx="12" cy="12" r="10"/><ellipse cx="12" cy="12" rx="4.5" ry="10"/><path d="M2 12h20M4 7h16M4 17h16"/></svg>
          www.lanternschool.com
        </li>
      </ul>
    </div>
    <p class="band-white">18, Maple Grove Road Brookfield 20914, Eastland</p>
    <span class="strip strip-green"></span>
    <span class="strip strip-blue"></span>
  </section>

</body>
</html>
```